Brisbane IT support business needs our first website

Hi All,

We are after a new website design for our IT solutions and support business.The business name is Harbourline Computing Services Group, or HCSG for short. We provide a range of solutions and services within the IT space.

I would like to utilize the two colours in our business logo I have uploaded.

I understand this is initially for the design only aspect of the site, but I would like to engage the winner to finish coding the website and finalize after also.

Target Market(s)

Other businesses owners and home users.

Industry/Entity Type

Business

Requirements
Must have
• Nice clean and functional design utilizing our business colours from the logo.

```html
<!DOCTYPE html>
<html lang="en">
<head>
<meta charset="utf-8">
<title>HCSG – Harbourline Computing Services Group</title>
<link href="https://fonts.googleapis.com/css2?family=Open+Sans:wght@400;600;700&family=PT+Sans:wght@400;700&display=swap" rel="stylesheet">
<style>
:root{
  --orange:#f47a20;
  --navy:#0d3b55;
  --blue:#2f86b4;
  --sky:#5aa9d3;
  --ink:#333;
  --muted:#777;
  --light:#f2f2f2;
  --footer:#262626;
  --footer-deep:#1c1c1c;
}
*{margin:0;padding:0;box-sizing:border-box}
html,body{width:772px;height:1200px;overflow:hidden;background:#fff}
body{position:relative;font-family:"Open Sans",sans-serif;color:var(--ink)}
.abs{position:absolute}
.site-header{left:0;top:0;width:772px;height:77px;border-top:3px solid var(--navy);background:#fff}
.brand{left:90px;top:14px;display:flex;align-items:center;gap:10px}
.brand-dot{width:48px;height:48px;border-radius:50%;background:var(--navy)}
.brand-name{font-family:"PT Sans",sans-serif;font-weight:700;font-size:26px;color:var(--orange);line-height:1}
.brand-full{font-family:"PT Sans",sans-serif;font-weight:700;font-size:5.5px;color:var(--navy);width:68px;line-height:1.2;margin-top:2px}
.main-nav{right:96px;top:35px;display:flex;gap:27px;font-size:8px;font-weight:600;color:#444;list-style:none}
.main-nav .active{color:var(--orange)}
.hero{left:0;top:77px;width:772px;height:326px;background:linear-gradient(100deg,#8cc6e4 0%,#3e92c2 40%,#1a5f8c 70%,#0b2f4b 100%)}
.hero-photo{left:330px;top:0;width:442px;height:326px;background:radial-gradient(ellipse at 40% 50%,rgba(200,235,255,.35),rgba(10,40,70,0) 60%)}
.hero-bubble{left:58px;top:63px;width:228px;height:228px;border-radius:50%;background:rgba(40,120,170,.75);text-align:center;color:#fff;padding:34px 22px 0}
.hero-bubble h1{font-family:"PT Sans",sans-serif;font-size:21px;font-weight:700;margin-bottom:10px}
.hero-bubble p{font-size:7.4px;line-height:15.6px}
.hero-more{display:inline-block;margin-top:8px;width:42px;height:42px;border-radius:50%;background:#fff;color:#555;font-size:8px;line-height:42px}
.slider-dots{right:48px;top:292px;display:flex;gap:5px}
.slider-dots span{width:7px;height:7px;border-radius:50%;background:#ddd}
.slider-dots span.on{background:var(--navy)}
.service{width:182px;height:158px;border-radius:50%;background:radial-gradient(circle at 50% 40%,#fff 55%,#ececec 100%);text-align:center;padding-top:10px;top:440px}
.service h2{font-family:"PT Sans",sans-serif;font-size:16px;font-weight:700;color:#333;margin:6px 0 6px}
.service p{font-size:7.4px;line-height:13.4px;color:var(--muted)}
.service a{display:block;margin-top:5px;font-size:6.6px;font-weight:700;color:var(--navy);text-decoration:none}
.divider{left:91px;top:620px;width:590px;border-top:1px dotted #ccc}
.section-title{font-family:"PT Sans",sans-serif;font-size:15.5px;font-weight:700;color:#333}
.photo{background:linear-gradient(135deg,#dfe7ee,#8ea7bd 55%,#3e5c7c);border:3px solid #fff;box-shadow:0 0 0 1px #ddd}
.welcome-lead{left:313px;top:682px;width:142px;font-size:7.2px;line-height:14.4px;color:var(--muted);text-align:justify}
.welcome-lead strong{display:block;color:var(--orange);font-weight:400;font-size:8px;margin-bottom:1px}
.welcome-body{left:93px;top:806px;width:360px;font-size:6.6px;line-height:14.4px;color:var(--muted)}
.news-item{left:486px;width:196px;height:52px;display:flex;gap:10px}
.news-item .photo{width:60px;height:50px;flex:none}
.news-item p{font-size:6.8px;line-height:13.4px;color:var(--muted)}
.news-item time{display:block;color:var(--orange);font-size:6.8px}
.partners{left:0;top:897px;width:772px;height:81px;background:var(--light)}
.partners span{position:absolute;top:22px;width:40px;height:38px;background:#3a3a3a;border-radius:50%}
.site-footer{left:0;top:978px;width:772px;height:172px;background:var(--footer);color:#ddd}
.site-footer h3{font-family:"PT Sans",sans-serif;font-weight:400;font-size:11.5px;color:#fff;position:absolute;top:32px}
.site-footer .col{position:absolute;top:62px;font-size:7px;line-height:11.6px}
.foot-nav{list-style:none;line-height:15.2px!important}
.foot-nav li::before{content:"»  "}
.field{width:136px;height:18px;background:#3a3a3a;border-radius:3px;font-size:7px;color:#ccc;padding:5px 6px;margin-bottom:8px}
.submit{display:inline-block;border:1px solid #fff;border-radius:3px;font-size:7px;font-weight:700;color:#fff;padding:5px 9px}
.footer-bar{left:0;top:1150px;width:772px;height:50px;background:var(--footer-deep);border-top:1px solid #333;color:#ccc}
.copy{left:97px;top:22px;font-size:7px}
.social{left:541px;top:14px;display:flex;gap:8px}
.social span{width:18px;height:18px;border-radius:50%;background:#444}
</style>
</head>
<body>
<header class="site-header abs">
  <div class="brand abs"><div class="brand-dot"></div><div><div class="brand-name">HCSG</div><div class="brand-full">Harbourline Computing Services Group</div></div></div>
  <ul class="main-nav abs"><li class="active">HOME</li><li>ABOUT US</li><li>SERVICES</li><li>BLOG</li><li>MEDIA</li><li>CONTACT US</li></ul>
</header>

<section class="hero abs">
  <div class="hero-photo abs" role="img" aria-label="Man touching a glowing interface of device icons"></div>
  <div class="hero-bubble abs">
    <h1>IT SOLUTIONS</h1>
    <p>Lorem ipsum dolor sit amet, consectetuer adipiscing elit. Aenean commodo ligula eget dolor. Aenean massa. Cum sociis natoque penatibus et magnis dis parturient montes, nascetur ridiculus mus. Donec quam felis, ultricies nec, pellentesque eu, pretium</p>
    <span class="hero-more">More</span>
  </div>
  <div class="slider-dots abs"><span class="on"></span><span></span><span></span></div>
</section>

<article class="service abs" style="left:91px">
  <svg width="24" height="26" viewBox="0 0 24 26"><circle cx="12" cy="8" r="6" fill="#f47a20"/><path d="M1 26c0-7 5-10 11-10s11 3 11 10z" fill="#f47a20"/></svg>
  <h2>IT SUPPORT</h2><p>Accusamu dolore massa<br>fugharum quidemed rerum facilis<br>iusto ssimos ducimus qui blanditii<br>stes es praesentiumvol.</p><a>READ MORE ›</a>
</article>
<article class="service abs" style="left:295px">
  <svg width="28" height="26" viewBox="0 0 28 26"><circle cx="14" cy="12" r="6" fill="#f47a20"/><rect x="11" y="19" width="6" height="5" fill="#f47a20"/><g stroke="#f47a20" stroke-width="2"><path d="M14 1v3M3 12h3M22 12h3M6 4l2 2M22 4l-2 2"/></g></svg>
  <h2>IT SOLUTIONS</h2><p>Accusamu dolore massa<br>fugharum quidemed rerum facilis<br>iusto ssimos ducimus qui blanditii<br>stes es praesentiumvol.</p><a>READ MORE ›</a>
</article>
<article class="service abs" style="left:499px">
  <svg width="32" height="26" viewBox="0 0 32 26"><rect x="2" y="2" width="22" height="16" fill="none" stroke="#f47a20" stroke-width="2"/><rect x="8" y="7" width="22" height="16" fill="#fff" stroke="#f47a20" stroke-width="2"/></svg>
  <h2>NETWORKING</h2><p>Accusamu dolore massa<br>fugharum quidemed rerum facilis<br>iusto ssimos ducimus qui blanditii<br>stes es praesentiumvol.</p><a>READ MORE ›</a>
</article>

<div class="divider abs"></div>

<h2 class="section-title abs" style="left:91px;top:646px">WELCOME TO &nbsp;HCSG</h2>
<div class="photo abs" style="left:92px;top:683px;width:198px;height:112px" role="img" aria-label="Team of office colleagues working at a laptop"></div>
<p class="welcome-lead abs"><strong>Consectetuer adipiscing elit. Aenean</strong>Commodo ligula eget dolor. Aenean massa. Cum sociis natoque penatibus et magnis dis parturient montes, nascetur ridiculus mus. Donec quam felis, ultricies nec, pellentesque eu, pretium quis, sem.Nulla consequat massa quis enim.Donec pede justo, fringilla .</p>
<p class="welcome-body abs">Consectetuer adipiscing elit. Aenean commodo ligula eget dolor. Aenean massa. Cum sociis natoque penatibus et magnis dis parturient montes, nascetur ridiculus mus. Donec quam felis, ultricies nec, pellentesque eu, pretium quis, sem.Nulla consequat massa quis enim. Donec pede justo, fringilla vel, aliquet nec, vulputate eget, arcu. In enim justo, rhoncus ut, imperdiet a, venenatis vitae, justo.</p>

<h2 class="section-title abs" style="left:486px;top:646px">LATEST NEWS</h2>
<div class="news-item abs" style="top:683px"><div class="photo" role="img" aria-label="Businesswoman at the office"></div><p><time>29.10.2014</time>Consectetuer adipiscing elit. Aenean commodo ligula eget dolor. Aenean massa. Cum sociis natoque</p></div>
<div class="news-item abs" style="top:748px"><div class="photo" role="img" aria-label="Business meeting around a table"></div><p><time>29.10.2014</time>Consectetuer adipiscing elit. Aenean commodo ligula eget dolor. Aenean massa. Cum sociis natoque</p></div>
<div class="news-item abs" style="top:813px"><div class="photo" role="img" aria-label="Hand signing a document"></div><p><time>29.10.2014</time>Consectetuer adipiscing elit. Aenean commodo ligula eget dolor. Aenean massa. Cum sociis natoque</p></div>

<section class="partners abs" aria-label="Partners">
  <span style="left:96px"></span><span style="left:168px;border-radius:4px"></span><span style="left:237px"></span><span style="left:310px"></span><span style="left:381px"></span><span style="left:456px"></span><span style="left:534px;border-radius:4px"></span><span style="left:612px;width:62px"></span>
</section>

<footer class="site-footer abs">
  <h3 style="left:97px">LATEST FROM BLOG</h3>
  <div class="col" style="left:97px;width:140px"><b style="font-size:7.5px;color:#fff">Post Title</b><br><span style="font-size:5.5px">Monday, 30th October 2014</span><p style="margin-top:6px">Vestibulumaccumsan egestibulum eu justo convallis augue estas aenean elit intesque sed. Facilispede estibulum nulla orna nisl velit elit ac aliquat non tincidunt. Namjusto cras urna</p></div>
  <h3 style="left:288px">NAVIGATION</h3>
  <ul class="col foot-nav" style="left:288px"><li>Home</li><li>About us</li><li>Services</li><li>News</li><li>Blog</li><li>Contact us</li></ul>
  <h3 style="left:392px">COMPANY DETAILS</h3>
  <div class="col" style="left:392px">Company Name<br>Street Name &amp; Number<br>Town<br>Postcode/Zip<br><br>Tel: 123 456 7890<br>Email: contact@hcsg.example</div>
  <h3 style="left:540px">NEWSLETTER</h3>
  <div class="col" style="left:540px;top:64px"><div class="field">Name</div><div class="field">Email</div><span class="submit">SUBMIT</span></div>
</footer>
<div class="footer-bar abs">
  <p class="copy abs">Copyright © 2014 HCSG - All Rights Reserved</p>
  <div class="social abs"><span></span><span></span><span></span><span></span><span></span></div>
</div>
</body>
</html>
```